Graphic design for a survey invitation campaign (3 assets)

Objective
Create an engaging and motivational graphic design for the "2024 KOVE Satisfaction Survey" campaign, aimed at encouraging the KOVE user community to share their insights and help shape the future of content.

FOCUS:
We need the graphics to be about creating the feeling of "Sharing your experience" and "Being heard", and not about taking the survey. Craft a visual narrative that encourages the KOVE user community to engage. This campaign seeks to transcend the mere act of taking a survey, focusing instead on the personal and collective impact of contributing insights.

DELIVERABLES
We need three assets using the same graphics:
1) a banner for our website (728 x 90 leaderboard banner)
2) a graph for a popup banner (Banner artwork is 33.5" x 90")
3) a postcard (4” x 6”)

COPY:
[Hero title] "Help Us Shape the Future of Content – Share Your KOVE Insights"
[Subtitle] The 2024 KOVE Satisfaction survey is ready. Join us to harness the collective experience of the KOVE user community.
[CTA] Take the Survey Now
Font: Poppins; convey professionalism. The main message should be prominent, with the subtext and CTA easily distinguishable.

Branding: Include the organization's logo and ensure the design aligns with brand guidelines to maintain consistency across the campaign.

Layout: Ensure a clean and organized layout with a clear hierarchy. The main message should capture immediate attention, followed by the subtext, and finally the CTA.

Visual and Stylistic Requirements: Imagery:
Use imagery that resonates with content creators and technical professionals. Consider incorporating abstract or symbolic representations of content creation, collaboration, and innovation.

Opt for visuals that represent diverse groups of professionals engaging in meaningful conversations. Elements such as open books, speech bubbles, or roundtable discussions can symbolize the sharing of knowledge and experiences.

Color Scheme: Opt for a professional yet inviting color palette. Use brand colors , supplemented by vibrant accents to highlight key elements like the CTA button.

Call to Action (CTA): Make the "Take the Survey Now!" button prominent and compelling. Use a contrasting color or design element to make it stand out.

Engagement Elements: Consider adding subtle animations or interactive elements (for digital formats) to make the CTA more engaging.

Design Inspirations:
Look at successful surveys and content strategy campaigns for inspiration, focusing on designs that effectively engage and motivate professional communities. Incorporate elements that symbolize growth, community, and insight, such as interconnected nodes or lightbulbs, to reflect the collective benefit of participating in the survey

Use our website for inspiration:
https://www.harborquillworks.com
Updates

Please see updates to the project brief for specific details on how to improve the designs. We appreciate your time and efforts.

Target Market(s)

KOVE users and professionals involved in content creation, management, and strategy. Individuals with experience in technical writing, documentation, and content strategy who are familiar with or interested in KOVE (Meridian Synthesis Module Layering).

Industry/Entity Type

We work in the technical documentation industry specializing in content data exchange model called KOVE.

Font styles to use
Sans Serif

Colors
0054AA
0677BA
7BADD7
CADEEF
E8F1F8
E54698
E96AAD
F1A4CE
F9D9EA
FCEFF6
6B429C
8869AF
B7A5CE
E3DAEB
F3F0F8

Requirements
Must have
• Copy for the Campaign: Main Message: "Help Us Shape the Future of Content – Share Your KOVE Insights" Subtext: "The 2024 KOVE Satisfaction survey is ready. Join us to harness the collective experience of the KOVE user community." Call to Action (CTA): "Take the Survey Now!"

```html
<!DOCTYPE html>
<html lang="en">
<head>
<meta charset="utf-8">
<title>2024 KOVE Satisfaction Survey – Campaign Assets</title>
<link href="https://fonts.googleapis.com/css2?family=Nunito:wght@400;800;900&display=swap" rel="stylesheet">
<style>
  :root{
    --navy:#1d1a8a;
    --magenta:#b43ccd;
    --violet:#a448d2;
    --sky:#6898e6;
    --ink:#111;
    --paper:#ffffff;
    --stage:#c9ccd0;
    --robot-light:#dfe2e8;
    --robot-dark:#3a3a44;
  }
  *{box-sizing:border-box;margin:0;padding:0}
  html,body{width:1200px;height:849px;overflow:hidden}
  body{background:var(--stage);font-family:"Nunito",sans-serif;position:relative;color:var(--navy)}

  .brand{display:flex;align-items:center;gap:6px}
  .brand-dot{width:34px;height:34px;border-radius:50%;background:linear-gradient(135deg,var(--sky),var(--navy))}
  .brand-name{font-weight:800;color:var(--navy);line-height:1;font-size:17px}

  .hero{font-weight:900;text-transform:uppercase;line-height:1.02;text-align:center;color:var(--navy)}
  .hero .accent{color:var(--magenta);display:block}

  .cta-bubble{position:absolute;background:var(--magenta);color:#fff;font-weight:900;text-transform:uppercase;text-align:center;line-height:1.05;border-radius:12px;transform:rotate(-10deg)}
  .illustration{position:absolute;background:linear-gradient(160deg,var(--robot-light) 0%,#b9bdc6 45%,var(--robot-dark) 100%);border-radius:18px}

  .survey-info{color:#fff;text-align:center}
  .survey-info .year{font-weight:900;text-transform:uppercase;line-height:1}
  .survey-info .sub{font-weight:400;line-height:1.2}
  .survey-info .join{font-weight:900;text-transform:uppercase;line-height:1.1}

  .plus{position:absolute;fill:var(--magenta)}

  /* Roll-up banner */
  .rollup{position:absolute;left:150px;top:118px;width:240px;height:594px;background:var(--paper);overflow:hidden}
  .rollup .pattern-band{position:absolute;left:0;top:0;width:240px;height:80px;background:linear-gradient(170deg,#e6e6f4 0%,#ffffff 80%)}
  .rollup .brand{position:absolute;left:82px;top:52px}
  .rollup .hero{position:absolute;left:0;width:240px;top:116px;font-size:26px}
  .rollup .wave{position:absolute;left:0;top:380px}
  .rollup .illustration{left:28px;top:262px;width:204px;height:204px;border-radius:30px 30px 60px 20px}
  .rollup .cta-bubble{left:36px;top:266px;width:84px;padding:8px 4px;font-size:13px}
  .rollup .survey-info{position:absolute;left:0;width:240px;top:476px}
  .rollup .survey-info .year{font-size:25px}
  .rollup .survey-info .sub{font-size:14px}
  .rollup .survey-info .join{font-size:17px;margin-top:6px}

  /* Website banner */
  .label{position:absolute;left:437px;width:733px;top:196px;text-align:center;font-size:11px;font-weight:800;color:var(--ink);letter-spacing:.5px}
  .web-banner{position:absolute;left:437px;top:217px;width:733px;height:90px;background:var(--paper);border:1px solid var(--navy);overflow:hidden}
  .web-banner .wave{position:absolute;left:0;top:0}
  .web-banner .survey-info{position:absolute;left:6px;top:6px;width:160px}
  .web-banner .survey-info .year{font-size:19px}
  .web-banner .survey-info .sub{font-size:10.5px}
  .web-banner .survey-info .join{font-size:13px;margin-top:5px}
  .web-banner .hero{position:absolute;left:230px;width:290px;top:14px;font-size:18px}
  .web-banner .brand{position:absolute;left:512px;top:22px}
  .web-banner .illustration{left:620px;top:0;width:112px;height:90px;border-radius:0}
  .web-banner .cta-bubble{left:630px;top:4px;width:46px;padding:4px 2px;font-size:7.5px;border-radius:6px}

  /* Postcard */
  .postcard{position:absolute;left:612px;top:368px;width:480px;height:320px;background:var(--paper);overflow:hidden}
  .postcard .stamp{position:absolute;right:28px;top:20px;width:44px;height:44px;border:2px dashed var(--ink)}
  .postcard .address-line{position:absolute;right:20px;width:140px;height:1px;background:var(--ink)}
  .postcard .hero{position:absolute;left:40px;width:240px;top:56px;font-size:25px;text-align:left}
  .postcard .wave{position:absolute;left:0;bottom:0}
  .postcard .survey-info{position:absolute;left:14px;bottom:12px;width:150px;text-align:left}
  .postcard .survey-info .year{font-size:15px}
  .postcard .survey-info .sub{font-size:9px}
  .postcard .survey-info .join{font-size:10px;margin-top:3px}
  .postcard .brand{position:absolute;left:200px;top:228px}
  .postcard .illustration{left:354px;top:176px;width:126px;height:144px;border-radius:20px 0 0 0}
  .postcard .cta-bubble{left:338px;top:178px;width:60px;padding:5px 2px;font-size:9px;border-radius:8px}
</style>
</head>
<body>

<!-- Roll-up banner -->
<section class="rollup" aria-label="Pop-up banner">
  <div class="pattern-band"></div>
  <div class="brand"><span class="brand-dot"></span><span class="brand-name">harbor<br>quill</span></div>
  <h1 class="hero">Help us shape<br>the future<br>of content<span class="accent">– share your<br>KOVE insights</span></h1>
  <svg class="wave" width="240" height="214" viewBox="0 0 240 214" aria-hidden="true">
    <defs><linearGradient id="gradRoll" x1="0" y1="0" x2="1" y2="0"><stop offset="0" stop-color="#a448d2"/><stop offset="1" stop-color="#6898e6"/></linearGradient></defs>
    <path d="M0 10 C60 -4 110 0 150 20 C190 40 215 20 240 8 L240 214 L0 214 Z" fill="url(#gradRoll)"/>
  </svg>
  <div class="illustration" role="img" aria-label="Illustration of a robot at a glowing digital console"></div>
  <div class="cta-bubble">Take the<br>survey<br>now!</div>
  <div class="survey-info">
    <p class="year">The 2024 KOVE</p>
    <p class="sub">Satisfaction survey is ready.</p>
    <p class="join">Join us to harness</p>
    <p class="sub">the collective experience of<br>the KOVE user community.</p>
  </div>
</section>

<!-- Website banner -->
<p class="label">WEBSITE BANNER</p>
<section class="web-banner" aria-label="Website banner">
  <svg class="wave" width="260" height="90" viewBox="0 0 260 90" aria-hidden="true">
    <defs><linearGradient id="gradWeb" x1="0" y1="0" x2="1" y2="1"><stop offset="0" stop-color="#6898e6"/><stop offset="1" stop-color="#a448d2"/></linearGradient></defs>
    <path d="M0 0 L155 0 C185 20 190 60 215 78 C228 86 240 88 260 90 L0 90 Z" fill="url(#gradWeb)"/>
  </svg>
  <svg class="plus" style="left:196px;top:2px" width="52" height="52" viewBox="0 0 52 52" aria-hidden="true"><rect x="20" y="0" width="12" height="52"/><rect x="0" y="20" width="52" height="12"/></svg>
  <div class="survey-info">
    <p class="year">The 2024 KOVE</p>
    <p class="sub">Satisfaction survey is ready.</p>
    <p class="join">Join us to harness</p>
    <p class="sub">the collective experience of<br>the KOVE user community.</p>
  </div>
  <h2 class="hero">Help us shape<br>the future of content<span class="accent">– share your KOVE insights</span></h2>
  <div class="brand"><span class="brand-dot"></span><span class="brand-name">harbor<br>quill</span></div>
  <div class="illustration" role="img" aria-label="Illustration of a robot at a glowing digital console"></div>
  <div class="cta-bubble">Take the<br>survey<br>now!</div>
</section>

<!-- Postcard -->
<section class="postcard" aria-label="Postcard">
  <div class="stamp"></div>
  <div class="address-line" style="top:96px"></div>
  <div class="address-line" style="top:114px"></div>
  <div class="address-line" style="top:132px"></div>
  <div class="address-line" style="top:150px"></div>
  <h2 class="hero">Help us shape<br>the future<br>of content<span class="accent">– share your<br>KOVE insights</span></h2>
  <svg class="wave" width="200" height="110" viewBox="0 0 200 110" aria-hidden="true">
    <defs><linearGradient id="gradCard" x1="0" y1="0" x2="1" y2="1"><stop offset="0" stop-color="#6898e6"/><stop offset="1" stop-color="#a448d2"/></linearGradient></defs>
    <path d="M0 20 C40 0 90 4 120 30 C150 60 165 95 200 110 L0 110 Z" fill="url(#gradCard)"/>
  </svg>
  <svg class="plus" style="left:8px;top:196px" width="40" height="40" viewBox="0 0 40 40" aria-hidden="true"><rect x="15" y="0" width="10" height="40"/><rect x="0" y="15" width="40" height="10"/></svg>
  <div class="survey-info">
    <p class="year">The 2024 KOVE</p>
    <p class="sub">Satisfaction survey is ready.</p>
    <p class="join">Join us to harness</p>
    <p class="sub">the collective experience of<br>the KOVE user community.</p>
  </div>
  <div class="brand"><span class="brand-dot"></span><span class="brand-name">harbor<br>quill</span></div>
  <div class="illustration" role="img" aria-label="Illustration of a robot at a glowing digital console"></div>
  <div class="cta-bubble">Take the<br>survey<br>now!</div>
</section>

</body>
</html>
```